KVM Contracting services . Building and maintenance services, optic fibre installation

Business cards and logo design.I need a logo that I can use on business cards ,workwear and on my vehicles. I would like the KVM to be the main or larger text and contracting services to be the smaller or less important text.I like monograms, modern designs and repeating patterns symbols. I am also a Gemini and my favourite number is 22 so if this can be any inspiration to help with the design. Am thinking of the using German flag colours as a his is my family’s heritage. And the other 2 main colours I wear is black and white.But any ideas are appreciated.I do not need a design that is trade specific but a design that could be used for any business.

Target Market(s)

General public

Contact Information for Business Card

KVM Contracting Services ( front of business card)

(Back of business card)
Darren Holtwick
0451907326
Maintenance services
Optic fibre and data installation

Logo Text

Logo can just be pattern or monogram or incorporate KVM . I like the gemini star sign and the number 22

Colors
ec1f27
000000
fbee3e
ffffff

Requirements
Must have
• Logo and KVM Contracting Services on the front of business card
Nice to have
• Possible use of German flag colours.
• Modern design.
• Design to be able to be used on black or white background as I want to put it on clothing

```html
<!DOCTYPE html>
<html lang="en">
<head>
<meta charset="utf-8">
<title>KVM Contracting Services – Business Card</title>
<link href="https://fonts.googleapis.com/css2?family=Jost:wght@500;600&family=Open+Sans:wght@400&display=swap" rel="stylesheet">
<style>
  :root {
    --bg: #3a3a3c;
    --card-light: #dedede;
    --ink: #141414;
    --red: #ec1f27;
    --red-deep: #ff1a00;
    --orange: #ff8a00;
    --yellow: #ffb300;
    --dark: #1a0d0d;
    --rule: #9a9a9a;
    --white: #ffffff;
  }
  * { margin: 0; padding: 0; box-sizing: border-box; }
  html, body {
    width: 1200px; height: 896px; overflow: hidden;
    background: var(--bg);
  }
  .sheet {
    width: 1200px; height: 896px;
    display: flex; flex-direction: column;
    align-items: center; justify-content: center; gap: 40px;
  }
  .card {
    position: relative;
    width: 620px; height: 378px;
    overflow: hidden;
    box-shadow: 0 10px 24px rgba(0,0,0,0.45);
  }

  /* Front */
  .card--front {
    background: linear-gradient(205deg, var(--dark) 0%, var(--red-deep) 45%, var(--orange) 80%, var(--yellow) 100%);
  }
  .wordmark {
    position: absolute;
    font-family: "Jost", sans-serif;
    font-weight: 600;
    line-height: 1;
  }
  .card--front .wordmark {
    left: 50%; top: 50%;
    transform: translate(-50%, -50%);
    text-align: center;
    color: var(--white);
  }
  .wordmark__name { display: block; font-size: 150px; letter-spacing: 2px; }
  .wordmark__tag {
    display: block; font-size: 30px; letter-spacing: 2px;
    text-transform: uppercase; margin-top: 6px;
  }

  /* Back */
  .card--back { background: var(--card-light); }
  .contact {
    position: absolute; left: 52px; top: 78px;
  }
  .contact__name {
    font-family: "Jost", sans-serif; font-weight: 500;
    font-size: 27px; letter-spacing: 1px; text-transform: uppercase;
    color: var(--red); line-height: 1;
  }
  .contact__phone {
    font-family: "Open Sans", sans-serif; font-size: 24px;
    color: var(--ink); margin-top: 2px; letter-spacing: 1px;
  }
  .contact__services {
    list-style: none; margin-top: 18px;
    font-family: "Open Sans", sans-serif; font-size: 17px;
    color: var(--ink); line-height: 1.3;
  }
  .contact__rule {
    position: absolute; left: 52px; right: 52px; top: 278px;
    height: 1px; background: var(--rule);
  }
  .card--back .wordmark {
    right: 48px; top: 60px; text-align: right; color: var(--ink);
  }
  .card--back .wordmark__name { font-size: 96px; }
  .card--back .wordmark__tag { font-size: 21px; margin-top: 4px; }
  .flag-edge {
    position: absolute; left: 0; right: 0; bottom: 0; height: 12px;
    display: block;
  }
</style>
</head>
<body>
<main class="sheet">
  <section class="card card--front" aria-label="Business card front">
    <div class="wordmark">
      <span class="wordmark__name">KVM</span>
      <span class="wordmark__tag">Contracting Services</span>
    </div>
  </section>

  <section class="card card--back" aria-label="Business card back">
    <div class="contact">
      <p class="contact__name">Darren Holtwick</p>
      <p class="contact__phone">0451907326</p>
      <ul class="contact__services">
        <li>Maintenance services</li>
        <li>Optic fibre and data installation</li>
      </ul>
    </div>
    <div class="wordmark">
      <span class="wordmark__name">KVM</span>
      <span class="wordmark__tag">Contracting Services</span>
    </div>
    <div class="contact__rule"></div>
    <svg class="flag-edge" viewBox="0 0 620 12" preserveAspectRatio="none" aria-hidden="true">
      <rect x="0" y="0" width="620" height="4" fill="#141414"/>
      <rect x="0" y="4" width="620" height="4" fill="#ec1f27"/>
      <rect x="0" y="8" width="620" height="4" fill="#ffb300"/>
    </svg>
  </section>
</main>
</body>
</html>
```